Animal Horse & Bedding Company Needs a Website Coded & Designed

We need a website for a new animal bedding and feed company that is visually grabbing and vibrant. We would like to see a website that displays trust, quality and confidence. Needs to be responsive and mobile friendly for all browsers and coded for both Android & IOS. SEO is also important.

Joomla or Wordpress – must be both desktop and mobile friendly with fast page load speed. Need the ability to edit ourselves in Wordpress or Joomla.

Full details attached below with some layout and content ideas.

Coding

Coded - Design and coding required

Number of Pages Required

5+ page

Font styles to use
Sans Serif

Requirements
Must have
• Needs to be responsive and mobile friendly for all browsers and coded for both Android & IOS. SEO is also important.

Wordpress – must be both desktop and mobile friendly with fast page load speed. Need the ability to edit ourselves in Wordpress.

Logo Colours:
Dark Brown
CMYK: 50 / 70 / 80 / 70
Pantone: 4625C

Orange
CMYK: 0 / 50 / 100 / 0
Pantone: 144C
Nice to have
• Use picture of building attached and super impose logo on building.

```html
<!DOCTYPE html>
<html lang="en">
<head>
<meta charset="utf-8">
<title>Meadowline – Bedding &amp; Feed</title>
<link rel="stylesheet" href="https://fonts.googleapis.com/css2?family=Oswald:wght@300;400&family=Catamaran:wght@400;500&display=swap">
<style>
:root{
  --brown:#3b2314;
  --orange:#f7941d;
  --bg:#e6e6e8;
  --text:#3a3330;
  --navy:#0d1530;
  --black:#050505;
  --white:#ffffff;
}
*{box-sizing:border-box;margin:0;padding:0}
html,body{width:1200px;height:4093px;overflow:hidden}
body{position:relative;background:var(--bg);font-family:"Catamaran",sans-serif;color:var(--text)}
.abs{position:absolute}
.display{font-family:"Oswald",sans-serif;font-weight:300;text-transform:uppercase;letter-spacing:1px}

/* header */
.site-header{left:0;top:0;width:1200px;height:92px;background:var(--bg);z-index:5}
.brand{left:111px;top:26px;display:flex;align-items:center;gap:10px}
.brand-dot{width:18px;height:18px;border-radius:50%;background:var(--orange)}
.brand-name{font-family:"Oswald",sans-serif;font-weight:400;font-size:30px;color:var(--brown);letter-spacing:2px;line-height:1}
.brand-tag{left:139px;top:64px;font-family:"Oswald",sans-serif;font-size:9px;letter-spacing:6px;color:var(--orange)}
.main-nav{top:38px;font-family:"Oswald",sans-serif;font-weight:300;font-size:19px;color:var(--brown)}
.main-nav.active{color:var(--orange)}
.quote-btn{left:1011px;top:0;width:189px;height:92px;background:var(--orange);color:var(--white);font-family:"Oswald",sans-serif;font-weight:300;font-size:25px;display:flex;align-items:center;justify-content:center}

/* hero */
.hero-photo{left:0;top:92px;width:1200px;height:690px;background:linear-gradient(180deg,#c9d6e4 0%,#e9eef3 25%,#8a9a76 45%,#6d7a5a 60%,#7e6f5e 80%,#5c6a48 100%)}
.hero-title{left:0;top:290px;width:1200px;text-align:center;font-family:"Oswald",sans-serif;font-weight:300;font-size:104px;color:var(--white);letter-spacing:4px;line-height:1}
.hero-arrow{top:337px;width:64px;height:64px;border:2px solid var(--white);border-radius:50%}
.hero-curve{left:0;top:600px}
.dots{top:686px;left:574px;display:flex;gap:8px;align-items:center}
.dots span{width:6px;height:6px;border-radius:50%;background:var(--white)}
.dots span.on{width:12px;height:12px;border:2px solid var(--orange);background:transparent}

/* text blocks */
.lead{left:160px;width:880px;text-align:center;font-size:17px;line-height:30px}
.divider{left:111px;top:1161px;width:978px;height:1px;background:#cfc9c6}
.divider-badge{left:571px;top:1133px;width:58px;height:58px;border-radius:50%;background:var(--brown);border:4px solid var(--white);box-shadow:0 0 0 1px #cfc9c6}
.section-title{left:0;width:1200px;text-align:center;font-size:48px;color:var(--brown);line-height:1}
.section-title .accent{color:var(--orange)}
.ornament{display:flex;align-items:center;gap:10px}
.ornament i{display:block;width:70px;height:2px;background:var(--orange)}
.ornament b{display:block;width:14px;height:14px;border-radius:50%;border:2px solid var(--orange)}

/* offer cards */
.card{top:1473px;width:292px;height:288px;background:var(--white);border:2px solid #f5c58b;border-radius:10px;text-align:center}
.card svg{position:absolute;left:111px;top:20px}
.card h3{position:absolute;top:136px;left:0;width:100%;font-family:"Oswald",sans-serif;font-weight:300;font-size:22px;color:var(--orange);text-transform:uppercase}
.card p{position:absolute;top:188px;left:40px;right:40px;font-size:16px;line-height:27px;color:#6b6461}

/* bedding */
.bedding-band{left:0;top:1894px;width:1200px;height:553px;background:linear-gradient(90deg,#b9b6b5,#cdcbcb 60%,#d6d4d4)}
.bedding-photo{left:0;top:1848px}
.feature-list{list-style:none;font-size:16px;color:var(--text)}
.feature-list li{position:relative;padding-left:36px;line-height:24px}
.feature-list li::before{content:"";position:absolute;left:0;top:8px;width:8px;height:8px;border-radius:50%;background:var(--brown)}
.btn{width:196px;height:51px;border-radius:26px;background:var(--orange);box-shadow:0 0 0 2px var(--bg),0 0 0 3px var(--brown);color:var(--white);font-family:"Oswald",sans-serif;font-weight:300;font-size:20px;display:flex;align-items:center;justify-content:center}

/* feed */
.feed-ring{left:167px;top:2786px;width:460px;height:460px;border-radius:50%;border:2px solid #8d8683}
.feed-photo{left:180px;top:2799px;width:434px;height:434px;border-radius:50%;background:linear-gradient(180deg,#9fc3e6 0%,#d9e2c7 45%,#d5b560 70%,#a86a2b 100%)}
.benefits-title{left:748px;top:2784px;font-size:30px;color:var(--brown)}

/* delivery + footer */
.delivery{left:0;top:3385px;width:1200px;height:420px;background:radial-gradient(ellipse at 50% 90%,#2a3560 0%,#141c3c 45%,var(--navy) 100%)}
.delivery-title{left:0;top:3478px;width:1200px;text-align:center;font-size:66px;color:var(--white);letter-spacing:3px;line-height:1}
.footer-curve{left:0;top:3640px}
.site-footer{left:0;top:3800px;width:1200px;height:293px;background:var(--black)}
.footer-name{left:0;top:3780px;width:1200px;text-align:center;font-family:"Oswald",sans-serif;font-weight:400;font-size:36px;color:var(--white);letter-spacing:4px;line-height:1}
.footer-tag{left:0;top:3830px;width:1200px;text-align:center;font-family:"Oswald",sans-serif;font-size:12px;letter-spacing:10px;color:var(--orange)}
.footer-nav{top:3878px;font-family:"Oswald",sans-serif;font-weight:300;font-size:21px;color:var(--orange)}
.social{top:3929px;width:52px;height:52px;border-radius:50%;border:2px solid var(--orange);display:flex;align-items:center;justify-content:center}
.footer-rule{left:111px;top:4020px;width:978px;height:1px;background:#3a3a3a}
.legal{top:4045px;font-size:13px;color:#d8d8d8}
.legal-sep{left:1010px;top:4030px;width:2px;height:30px;background:var(--orange)}
</style>
</head>
<body>

<header class="abs site-header">
  <div class="abs brand"><span class="brand-dot"></span><span class="brand-name">MEADOWLINE</span></div>
  <div class="abs brand-tag">BEDDING &amp; FEED</div>
  <nav>
    <a class="abs main-nav active" style="left:457px">HOME</a>
    <a class="abs main-nav" style="left:556px">ABOUT</a>
    <a class="abs main-nav" style="left:660px">FEED</a>
    <a class="abs main-nav" style="left:756px">BEDDING</a>
    <a class="abs main-nav" style="left:879px">CONTACT US</a>
  </nav>
  <a class="abs quote-btn">REQUEST QUOTE</a>
</header>

<section>
  <div class="abs hero-photo" role="img" aria-label="Aerial view of red barns and stables surrounded by fenced paddocks and fields"></div>
  <h1 class="abs hero-title">MEADOWLINE</h1>
  <div class="abs hero-arrow" style="left:19px"><svg width="60" height="60" viewBox="0 0 60 60"><path d="M34 21 L25 30 L34 39" fill="none" stroke="#fff" stroke-width="3"/></svg></div>
  <div class="abs hero-arrow" style="left:1117px"><svg width="60" height="60" viewBox="0 0 60 60"><path d="M26 21 L35 30 L26 39" fill="none" stroke="#fff" stroke-width="3"/></svg></div>
  <svg class="abs hero-curve" width="1200" height="190" viewBox="0 0 1200 190">
    <path d="M0 43 Q600 200 1200 43 L1200 190 L0 190 Z" fill="#f7941d"/>
    <path d="M0 70 Q600 230 1200 70 L1200 190 L0 190 Z" fill="#e6e6e8"/>
    <path d="M0 95 Q600 262 1200 95" fill="none" stroke="#3b2314" stroke-width="2"/>
  </svg>
  <div class="abs dots"><span class="on"></span><span></span><span></span><span></span></div>
</section>

<section>
  <p class="abs lead" style="top:862px">Looking for the best bedding and feed for your horse, livestock or household pet look no further.&nbsp; We use premium locally sourced straw and hay in all of our products and are committed in providing quality products and service.</p>
  <p class="abs lead" style="top:982px">Your animal deserves the very best in health and comfort to keep them healthy, strong and happy.&nbsp; Our products are designed for horses, livestock (goats, cattle and sheep), small caged animals (rabbits, guinea pigs and more).</p>
  <div class="abs divider"></div>
  <div class="abs divider-badge"></div>
</section>

<section>
  <h2 class="abs display section-title" style="top:1244px">OUR <span class="accent">OFFER</span></h2>
  <div class="abs ornament" style="left:508px;top:1300px"><i></i><b></b><i></i></div>
  <p class="abs lead" style="top:1334px;left:170px;width:860px">The Meadowline offers supply and delivery of fresh bedding as well as removal of waste bedding.&nbsp; Let us deliver you a container of fresh straw and haul your waste bedding away.&nbsp; A full service solution that is sustainable and responsible.</p>

  <div class="abs card" style="left:111px">
    <svg width="70" height="80" viewBox="0 0 70 80"><path d="M35 4 L64 14 V38 C64 58 50 70 35 76 C20 70 6 58 6 38 V14 Z" fill="none" stroke="#3b2314" stroke-width="3"/><path d="M35 14 L56 21 V39 C56 53 46 62 35 67 C24 62 14 53 14 39 V21 Z" fill="none" stroke="#3b2314" stroke-width="2"/><circle cx="35" cy="40" r="12" fill="none" stroke="#f7941d" stroke-width="3"/><path d="M29 40 L34 45 L42 35" fill="none" stroke="#f7941d" stroke-width="3"/></svg>
    <h3>Quality Guaranteed</h3>
    <p>Grown for quality - 100% natural with no chemicals or additives</p>
  </div>
  <div class="abs card" style="left:454px">
    <svg width="84" height="80" viewBox="0 0 84 80"><rect x="4" y="24" width="64" height="42" fill="none" stroke="#3b2314" stroke-width="3"/><path d="M4 24 L36 50 L68 24 M4 66 L28 44 M68 66 L44 44" fill="none" stroke="#3b2314" stroke-width="2"/><circle cx="66" cy="20" r="14" fill="#f7941d"/><text x="66" y="25" text-anchor="middle" font-family="Oswald,sans-serif" font-size="14" fill="#fff">24</text></svg>
    <h3>Full Service Solution</h3>
    <p>Dedicated in providing a full service solution of bedding supply &amp; waste removal</p>
  </div>
  <div class="abs card" style="left:791px">
    <svg width="76" height="80" viewBox="0 0 76 80"><g fill="none" stroke="#3b2314" stroke-width="2"><rect x="6" y="50" width="10" height="20"/><rect x="20" y="44" width="10" height="26"/><rect x="34" y="38" width="10" height="32"/><rect x="48" y="32" width="10" height="38"/><rect x="62" y="26" width="10" height="44"/></g><path d="M8 40 L30 30 L44 24 L62 10" fill="none" stroke="#f7941d" stroke-width="3"/><path d="M54 8 L66 7 L64 19" fill="none" stroke="#f7941d" stroke-width="3"/></svg>
    <h3>Convenient &amp; Cost Effective</h3>
    <p>Compressed bags , pellets or bulk products saving in shipping costs</p>
  </div>
</section>

<section>
  <div class="abs bedding-band" role="img" aria-label="Faded photo of a horse standing in mist behind the bedding details"></div>
  <svg class="abs bedding-photo" width="1200" height="642" viewBox="0 0 1200 642" role="img" aria-label="Mare and foal standing in tall green grass under a blue sky">
    <defs><linearGradient id="meadow" x1="0" y1="0" x2="0" y2="1"><stop offset="0" stop-color="#2f8fd0"/><stop offset="0.45" stop-color="#8cc4e6"/><stop offset="0.62" stop-color="#5f8a3a"/><stop offset="1" stop-color="#3f6d22"/></linearGradient></defs>
    <path d="M588 0 L1200 0 L1200 642 L588 642 C520 470 520 180 588 0 Z" fill="url(#meadow)"/>
  </svg>
  <h2 class="abs display" style="left:111px;top:1928px;font-size:48px;color:var(--brown);line-height:1">BEDDING</h2>
  <div class="abs ornament" style="left:111px;top:1986px"><i style="width:40px"></i><b></b><i style="width:40px"></i></div>
  <ul class="abs feature-list" style="left:111px;top:2040px">
    <li style="margin-bottom:17px">100% Natural Chopped Straw</li>
    <li style="margin-bottom:17px">Low Dust</li>
    <li style="margin-bottom:17px">Chemical &amp; Additive Free</li>
    <li style="margin-bottom:17px">Clean &amp; Highly Absorbent</li>
    <li style="margin-bottom:17px">Cheaper than Wood Shavings</li>
    <li style="margin-bottom:17px">Economic – less used and less wasted</li>
    <li>Environmentally Friendly –<br>Recyclable &amp; Compostable</li>
  </ul>
  <a class="abs btn" style="left:113px;top:2357px">LEARN MORE</a>
</section>

<section>
  <h2 class="abs display section-title" style="top:2574px">FEED</h2>
  <div class="abs ornament" style="left:533px;top:2630px"><i style="width:45px"></i><b></b><i style="width:45px"></i></div>
  <p class="abs lead" style="top:2669px;left:150px;width:900px">Hay cubes and pellets are made from premium hay offering a variety of animals a feed that is non-GMO and packed with natural nutrients.&nbsp; These pellets and cubes are less bulky to handle, store and ship. As well, they reduce the amount of wasted feed.</p>
  <div class="abs feed-ring"></div>
  <div class="abs feed-photo" role="img" aria-label="Chestnut horse with a flowing blonde mane against a bright field"></div>
  <h3 class="abs display benefits-title">BENEFITS</h3>
  <ul class="abs feature-list" style="left:748px;top:2834px">
    <li style="margin-bottom:15px">100% Natural</li>
    <li style="margin-bottom:15px">Chemical &amp; Additive Free</li>
    <li style="margin-bottom:15px">Available in Pellets or Cubes</li>
    <li style="margin-bottom:15px">High Protein Content</li>
    <li style="margin-bottom:15px">Eliminate Waste In Feeding</li>
    <li style="margin-bottom:15px">Clean - Eliminates Dust From<br>Feeding Baled Hay</li>
    <li style="margin-bottom:15px">Cost Effective</li>
    <li style="margin-bottom:15px">Convenient</li>
    <li>Less wasted feed</li>
  </ul>
  <a class="abs btn" style="left:750px;top:3243px">LEARN MORE</a>
</section>

<section>
  <div class="abs delivery" role="img" aria-label="Night view of the globe with glowing delivery routes across North America"></div>
  <h2 class="abs display delivery-title">DELIVERY IN <span style="color:var(--orange)">CANADA</span> &amp; <span style="color:var(--orange)">USA</span></h2>
  <svg class="abs footer-curve" width="1200" height="170" viewBox="0 0 1200 170">
    <path d="M0 100 Q600 -40 1200 100" fill="none" stroke="#ffffff" stroke-width="1.5"/>
    <path d="M0 128 Q600 -6 1200 128 L1200 170 L0 170 Z" fill="#f7941d"/>
    <path d="M0 145 Q600 12 1200 145 L1200 170 L0 170 Z" fill="#050505"/>
  </svg>
</section>

<footer>
  <div class="abs site-footer"></div>
  <div class="abs footer-name">MEADOWLINE</div>
  <div class="abs footer-tag">BEDDING &amp; FEED</div>
  <nav>
    <a class="abs footer-nav" style="left:346px">HOME</a>
    <a class="abs footer-nav" style="left:444px">ABOUT</a>
    <a class="abs footer-nav" style="left:548px">FEED</a>
    <a class="abs footer-nav" style="left:644px">BEDDING</a>
    <a class="abs footer-nav" style="left:766px">CONTACT US</a>
  </nav>
  <div class="abs social" style="left:498px"><svg width="22" height="22" viewBox="0 0 24 24"><path d="M6 3 L9 3 L11 8 L8.5 9.5 C9.5 12 12 14.5 14.5 15.5 L16 13 L21 15 L21 18 C21 19.5 19.5 21 18 21 C10 20.5 3.5 14 3 6 C3 4.5 4.5 3 6 3 Z" fill="none" stroke="#f7941d" stroke-width="1.8"/></svg></div>
  <div class="abs social" style="left:573px"><svg width="22" height="22" viewBox="0 0 24 24"><rect x="3" y="6" width="18" height="13" fill="none" stroke="#f7941d" stroke-width="1.8"/><path d="M3 6 L12 13 L21 6" fill="none" stroke="#f7941d" stroke-width="1.8"/></svg></div>
  <div class="abs social" style="left:651px"><svg width="22" height="22" viewBox="0 0 24 24"><rect x="4" y="4" width="16" height="16" rx="3" fill="none" stroke="#f7941d" stroke-width="1.8"/></svg></div>
  <div class="abs footer-rule"></div>
  <p class="abs legal" style="left:111px">Copyrights ©2021 the meadowline. All Rights Reserved</p>
  <a class="abs legal" style="left:900px">Privacy Policy</a>
  <div class="abs legal-sep"></div>
  <a class="abs legal" style="left:1035px">Sitemap</a>
</footer>

</body>
</html>
```